Business Card Design Project

I require a business card with the following information on them for various different people;
name
m:
f:
e:
I have a logo already and will attached that. We are in the construction industry. I require something clean and simple but eye catching at the same time. You can use another colour with our logo if you like and you can style the logo as well if you wish. I am open.
Also it needs to be front and back design.
Industry/Entity Type
Construction
Requirements
Must have
- Logo, name, mobile, fax and email address.
Front and back design

```html
<!DOCTYPE html>
<html lang="en">
<head>
<meta charset="utf-8">
<title>Stonefield Builders – Business Cards</title>
<link rel="stylesheet" href="https://fonts.googleapis.com/css2?family=Open+Sans:wght@400;600;700&display=swap">
<style>
  :root {
    --page-bg: #e9e6e1;
    --card-white: #ffffff;
    --brand-green: #4fae44;
    --brand-green-light: #b6d957;
    --brand-green-mid: #7cc247;
    --ink-text: #444444;
    --band-dark: #151515;
    --band-grey: #4a4b4e;
    --card-edge: #3b3b3b;
  }
  * { margin: 0; padding: 0; box-sizing: border-box; }
  html, body {
    width: 1200px; height: 757px; overflow: hidden;
    background: var(--page-bg);
    font-family: "Open Sans", Arial, sans-serif;
  }
  .canvas { position: relative; width: 1200px; height: 757px; }

  .card {
    position: absolute;
    width: 513px; height: 292px;
    border-radius: 14px;
    overflow: hidden;
    background: var(--card-white);
    border: 1px solid var(--card-edge);
  }
  .card--front { left: 49px; top: 205px; }
  .card--back  { left: 621px; top: 62px; }
  .card--green {
    left: 621px; top: 400px;
    border: none;
    background: radial-gradient(circle at 48% 40%, var(--brand-green-light) 0%, var(--brand-green-mid) 40%, var(--brand-green) 75%);
  }

  .brand {
    position: absolute; left: 0; right: 0;
    display: flex; align-items: center; justify-content: center; gap: 12px;
  }
  .brand__mark { width: 22px; height: 22px; background: var(--brand-green); }
  .brand__name {
    font-weight: 600; font-size: 34px; letter-spacing: 0.5px;
    color: var(--brand-green); white-space: nowrap;
  }
  .card--front .brand { top: 52px; }
  .card--back .brand { top: 120px; }
  .card--back .brand__name { font-size: 38px; }
  .card--green .brand { top: 120px; gap: 14px; }
  .card--green .brand__mark { width: 34px; height: 34px; background: var(--card-white); }
  .card--green .brand__name { font-size: 36px; color: var(--card-white); }

  .contact {
    position: absolute; top: 165px; left: 0; right: 0;
    text-align: center; font-size: 12.5px; color: var(--ink-text); line-height: 25px;
  }
  .contact__row { display: flex; justify-content: center; align-items: center; gap: 16px; }
  .contact__item { display: inline-flex; align-items: center; gap: 5px; }
  .contact__icon { width: 10px; height: 10px; fill: var(--ink-text); }

  .footer-rule {
    position: absolute; left: 0; right: 0; bottom: 50px; height: 6px;
    background: var(--brand-green);
  }
  .footer-band {
    position: absolute; left: 0; right: 0; bottom: 0; height: 46px;
    background: linear-gradient(90deg, var(--band-dark), var(--band-grey) 50%, var(--band-dark));
    display: flex; align-items: center; padding-left: 40px;
  }
  .holder { font-weight: 700; font-size: 15px; color: var(--brand-green); }
</style>
</head>
<body>
<main class="canvas">

  <section class="card card--front" aria-label="Card front">
    <div class="brand">
      <span class="brand__mark"></span>
      <span class="brand__name">Stonefield Builders</span>
    </div>
    <div class="contact">
      <div class="contact__row">
        <span class="contact__item">
          <svg class="contact__icon" viewBox="0 0 10 10" aria-hidden="true"><rect x="2.5" y="0" width="5" height="10" rx="1"/><rect x="3.5" y="1.5" width="3" height="5" fill="#fff"/></svg>
          +91 98765 43210
        </span>
        <span class="contact__item">
          <svg class="contact__icon" viewBox="0 0 10 10" aria-hidden="true"><rect x="2.5" y="0.5" width="5" height="3"/><rect x="0" y="3.5" width="10" height="5" rx="1"/></svg>
          +91 98765 43210
        </span>
      </div>
      <div class="contact__row">
        <span class="contact__item">
          <svg class="contact__icon" viewBox="0 0 10 10" aria-hidden="true"><rect x="0" y="2" width="10" height="6.5"/><path d="M0 2 L5 6 L10 2" fill="none" stroke="#fff" stroke-width="1"/></svg>
          office@stonefieldmail.com
        </span>
      </div>
    </div>
    <div class="footer-rule"></div>
    <div class="footer-band">
      <span class="holder">Your Name , Title</span>
    </div>
  </section>

  <section class="card card--back" aria-label="Card back">
    <div class="brand">
      <span class="brand__mark"></span>
      <span class="brand__name">Stonefield Builders</span>
    </div>
  </section>

  <section class="card card--green" aria-label="Card back, green variant">
    <div class="brand">
      <span class="brand__mark"></span>
      <span class="brand__name">Stonefield Builders</span>
    </div>
  </section>

</main>
</body>
</html>
```